Landscape design build company door flyer

I would like this flyer to convey a high-level of professionalism for a company that is excellent with communication with their clients as well as a company that does incredible installations

Went on vacation/holiday

```html
<!DOCTYPE html>
<html lang="en">
<head>
<meta charset="utf-8">
<title>Cedarline Builders – Outdoor Living Flyer</title>
<link rel="stylesheet" href="https://fonts.googleapis.com/css2?family=Montserrat:wght@500;600;700;800&family=Playfair+Display:wght@600&display=swap">
<style>
  :root {
    --navy: #0e2a40;
    --navy-deep: #0a2234;
    --gold: #f5aa0c;
    --white: #ffffff;
    --panel-grey: #efefef;
    --page-bg: #e9e9ea;
    --steel: #5d6d7c;
  }
  * { box-sizing: border-box; margin: 0; padding: 0; }
  html, body { width: 1200px; height: 1029px; overflow: hidden; background: var(--page-bg); }
  body { font-family: "Montserrat", sans-serif; position: relative; }

  .flyer {
    position: absolute; left: 219px; top: 24px;
    width: 762px; height: 980px;
    background: var(--navy);
    overflow: hidden;
    box-shadow: 0 10px 30px rgba(0,0,0,.18);
  }
  .top-band { position: absolute; left: 0; top: 0; width: 100%; height: 49px; background: var(--white); }
  .brand-frame { position: absolute; left: 0; top: 0; width: 762px; height: 134px; }
  .brand {
    position: absolute; left: 285px; top: 0; width: 183px; height: 134px;
    display: flex; flex-direction: column; align-items: center; justify-content: center; gap: 4px;
  }
  .brand-mark { width: 26px; height: 26px; border-radius: 50%; background: var(--navy); }
  .brand-name { font-family: "Montserrat", sans-serif; font-weight: 700; font-size: 15px; color: var(--navy); letter-spacing: .2px; }
  .brand-tag { font-weight: 700; font-size: 7.5px; color: var(--navy); letter-spacing: .2px; }

  .headline {
    position: absolute; left: 0; top: 164px; width: 100%;
    text-align: center; font-weight: 800; font-size: 44px; line-height: 47px;
    color: var(--white); letter-spacing: -.3px;
  }
  .headline .accent { color: var(--gold); }

  .about { position: absolute; left: 60px; top: 342px; width: 264px; color: var(--white); }
  .about h2 { font-weight: 700; font-size: 18px; margin-bottom: 8px; }
  .about p { font-weight: 500; font-size: 11.3px; line-height: 14.5px; text-align: justify; hyphens: auto; }
  .about p + p { margin-top: 14.5px; }

  .photo { position: absolute; }
  .photo-firepit { left: 361px; top: 348px; width: 127px; height: 128px; background: linear-gradient(160deg, #3d4650, #5a5550 55%, #8a6a3a); }
  .photo-pool { left: 499px; top: 348px; width: 204px; height: 128px; background: linear-gradient(135deg, #dfe5e6, #b9c6c8 45%, #3fb3b0 55%, #cfd7d8); }
  .photo-garage { left: 361px; top: 485px; width: 127px; height: 89px; background: linear-gradient(180deg, #8f8677, #8b4a22 45%, #9a8f84 75%, #7c7468); }
  .photo-steps { left: 361px; top: 583px; width: 127px; height: 89px; background: linear-gradient(180deg, #6a5a45, #55595c 35%, #3c4044); }
  .photo-aerial { left: 499px; top: 485px; width: 204px; height: 187px; background: linear-gradient(160deg, #4e5f44, #7b7f83 45%, #4a4f55 70%, #5a4030); }

  .services {
    position: absolute; left: 0; top: 688px; width: 100%; height: 169px;
    background: linear-gradient(90deg, #ffffff 0%, #ffffff 45%, #d3d6d9 68%, #6d7a86 88%, var(--navy) 100%);
  }
  .services h2 { position: absolute; left: 60px; top: 11px; font-weight: 700; font-size: 18px; color: var(--navy); }
  .service { position: absolute; display: flex; align-items: center; gap: 9px; font-weight: 700; font-size: 11px; color: var(--navy); letter-spacing: .2px; }
  .service svg { width: 26px; height: 26px; flex: none; }
  .badge { position: absolute; left: 586px; top: 34px; width: 116px; height: 116px; }

  .contact { position: absolute; left: 0; top: 857px; width: 100%; height: 117px; background: var(--navy); }
  .contact h2 { position: absolute; left: 60px; top: 15px; font-weight: 700; font-size: 16px; color: var(--white); }
  .phone { position: absolute; left: 58px; top: 38px; display: flex; align-items: center; gap: 12px; font-weight: 700; font-size: 40px; color: var(--gold); letter-spacing: -.5px; }
  .phone svg { width: 38px; height: 38px; }
  .email { position: absolute; right: 30px; top: 50px; font-weight: 500; font-size: 15px; color: var(--white); letter-spacing: .3px; }
  .bottom-strip { position: absolute; left: 0; top: 974px; width: 100%; height: 6px; background: var(--white); }
</style>
</head>
<body>
<main class="flyer">
  <div class="top-band"></div>
  <svg class="brand-frame" viewBox="0 0 762 134" aria-hidden="true">
    <polygon points="224,0 529,0 529,49 468,134 285,134 224,49" fill="var(--panel-grey)"/>
    <polygon points="224,49 285,134 285,49" fill="var(--navy)"/>
    <polygon points="529,49 468,134 468,49" fill="var(--navy)"/>
    <rect x="285" y="0" width="183" height="134" fill="var(--white)"/>
    <line x1="285.5" y1="134" x2="285.5" y2="168" stroke="#000" stroke-width="1"/>
    <line x1="467.5" y1="134" x2="467.5" y2="168" stroke="#000" stroke-width="1"/>
  </svg>
  <div class="brand">
    <span class="brand-mark"></span>
    <span class="brand-name">CEDARLINE BUILDERS</span>
    <span class="brand-tag">OUTDOOR LIVING SPACES</span>
  </div>

  <h1 class="headline">LET’S CREATE<br><span class="accent">YOUR DREAM OUTDOOR</span><br>LIVING SPACE!</h1>

  <section class="about">
    <h2>ABOUT US</h2>
    <p>Discover the endless possibilities for your outdoor space with The Cedarline Builders Team. Our team of skilled artisans is dedicated to turning your outdoor space into a breathtaking oasis that you’ll love coming home to. Whether it’s a cozy patio for intimate gatherings, a sprawling deck to host memorable parties, or a custom paver driveway that adds instant curb appeal, our high-quality craftsmanship ensures stunning results that exceed your expectations.</p>
    <p>From concept to completion, we take pride in every detail, using the finest materials to withstand Seattle’s climate while adding timeless elegance to your property. Embrace the Pacific Northwest lifestyle and create cherished moments with family and friends in a captivating outdoor haven.</p>
  </section>

  <div class="photo photo-firepit" role="img" aria-label="Evening paver patio with sunken fire pit, lit seat walls and pool"></div>
  <div class="photo photo-pool" role="img" aria-label="Aerial view of a rectangular pool framed by grey composite decking"></div>
  <div class="photo photo-garage" role="img" aria-label="Paver driveway in front of stone garage with wooden doors"></div>
  <div class="photo photo-steps" role="img" aria-label="Stone retaining wall with built-in steps"></div>
  <div class="photo photo-aerial" role="img" aria-label="Aerial view of a home with new paver driveway and landscaped beds"></div>

  <section class="services">
    <h2>OUR SERVICES</h2>
    <svg width="0" height="0" style="position:absolute" aria-hidden="true">
      <symbol id="house" viewBox="0 0 26 26">
        <path d="M2 11 L13 2 L24 11 V24 H2 Z" fill="none" stroke="currentColor" stroke-width="2" stroke-linejoin="round"/>
      </symbol>
    </svg>
    <div class="service" style="left:60px;top:52px"><svg viewBox="0 0 26 26"><use href="#house"/><rect x="8" y="12" width="10" height="8" fill="none" stroke="currentColor" stroke-width="1.4"/></svg>Paver Patios</div>
    <div class="service" style="left:60px;top:90px"><svg viewBox="0 0 26 26"><use href="#house"/><polygon points="6,21 10,14 16,14 20,21" fill="currentColor"/></svg>Paver Driveways</div>
    <div class="service" style="left:60px;top:130px"><svg viewBox="0 0 26 26"><use href="#house"/><rect x="7" y="11" width="6" height="4" fill="currentColor"/><rect x="11" y="15" width="6" height="4" fill="currentColor"/></svg>Retaining Walls</div>
    <div class="service" style="left:222px;top:52px"><svg viewBox="0 0 26 26"><use href="#house"/><path d="M7 18 q2-2 4 0 t4 0 t4 0 M7 21 q2-2 4 0 t4 0 t4 0" fill="none" stroke="currentColor" stroke-width="1.3"/></svg>Pools</div>
    <div class="service" style="left:222px;top:90px"><svg viewBox="0 0 26 26"><use href="#house"/><path d="M7 13 H19 M8 13 V21 M18 13 V21 M11 13 V21 M15 13 V21" stroke="currentColor" stroke-width="1.3"/></svg>Decks &amp; Railings</div>
    <div class="service" style="left:222px;top:131px"><svg viewBox="0 0 26 26"><use href="#house"/><path d="M8 21 V15 L13 11 L18 15 V21 Z" fill="currentColor"/></svg>Firepits &amp; Fireplaces</div>
    <div class="service" style="left:390px;top:52px"><svg viewBox="0 0 26 26"><use href="#house"/><rect x="11" y="11" width="4" height="6" rx="1" fill="none" stroke="currentColor" stroke-width="1.3"/><line x1="13" y1="17" x2="13" y2="21" stroke="currentColor" stroke-width="1.3"/></svg>Outdoor Lighting</div>
    <div class="service" style="left:390px;top:90px"><svg viewBox="0 0 26 26"><use href="#house"/><circle cx="13" cy="16" r="5" fill="none" stroke="currentColor" stroke-width="1.3"/><path d="M13 13 V19 M10 16 H16" stroke="currentColor" stroke-width="1.3"/></svg>And More...</div>
    <svg class="badge" viewBox="0 0 116 116" role="img" aria-label="Experience seal">
      <circle cx="58" cy="58" r="57" fill="#d9a21a"/>
      <circle cx="58" cy="58" r="44" fill="#2a2a2a"/>
      <circle cx="58" cy="58" r="38" fill="#e8b53a"/>
    </svg>
  </section>

  <section class="contact">
    <h2>CONTACT US TODAY</h2>
    <div class="phone">
      <svg viewBox="0 0 40 40" aria-hidden="true">
        <path d="M9 5 L15 5 L17 13 L13 16 C15 21 19 25 24 27 L27 23 L35 25 L35 31 C35 34 32 36 29 35 C17 32 8 23 5 11 C4 8 6 5 9 5 Z" fill="var(--gold)"/>
        <path d="M22 10 a8 8 0 0 1 8 8 M22 4 a14 14 0 0 1 14 14" fill="none" stroke="var(--gold)" stroke-width="2.5" stroke-linecap="round"/>
      </svg>
      <span>[206]-555-0148</span>
    </div>
    <span class="email">info@cedarlinebuilders.com</span>
  </section>
  <div class="bottom-strip"></div>
</main>
</body>
</html>
```